Paraffin Wax Packaging Design for Nail and Beauty Industry

We need an attractive design for the packaging of our new product, Paraffin Wax. Our company is a wholesale beauty/nail supply company that has been selling to nail salons in the US market for 10 years. We currently sell this product that we buy from another company. Now we want to launch our own brand of Paraffin Wax.

Target Market(s)

Retail nail salons in the US market.

Industry/Entity Type

Industry

Font styles to use
Sans Serif

Colors

Designer to choose colors to be used in the design.

Requirements
Must have
• Our logo (attached).
• All information on the "Ingredient List" (attached).
• Design for Clear Packaging so product can show through.
• Design for Package Dimensions of 4.25" x 11" (110cm x 280 cm).
Nice to have
• Picture related to women's skin and or beauty.
• Contrast as in the design of product that we currently sell (attached).

```html
<!DOCTYPE html>
<html lang="en">
<head>
<meta charset="utf-8">
<title>By Selvane – Paraffin Wax Package</title>
<link rel="stylesheet" href="https://fonts.googleapis.com/css2?family=Arimo:wght@400&family=Bodoni+Moda:wght@400;700&family=Yellowtail&display=swap">
<style>
  :root {
    --backdrop: #e9e9ec;
    --panel: #ffffff;
    --indigo: #3f3d8f;
    --royal: #4a6fd6;
    --wave-start: #4b74d8;
    --wave-end: #3f479f;
    --ink-dark: #1c1c1c;
    --white: #ffffff;
    --skin-light: #f3dccd;
    --skin-mid: #e7c0a8;
  }
  html, body {
    margin: 0;
    padding: 0;
    width: 1200px;
    height: 2400px;
    overflow: hidden;
    background: var(--backdrop);
  }
  .canvas {
    position: relative;
    width: 1200px;
    height: 2400px;
    overflow: hidden;
  }
  .package {
    position: absolute;
    left: 152px;
    top: 40px;
    width: 500px;
    height: 1295px;
    background: var(--panel);
    overflow: hidden;
    transform: scale(1.792);
    transform-origin: top left;
    box-shadow: 0 2px 6px rgba(0,0,0,0.12);
  }
  .package-shapes {
    position: absolute;
    inset: 0;
    width: 500px;
    height: 1295px;
  }
  .brand-name {
    position: absolute;
    top: 52px;
    left: 0;
    width: 500px;
    text-align: center;
    font-family: "Bodoni Moda", "Times New Roman", serif;
    font-weight: 700;
    font-size: 54px;
    color: var(--ink-dark);
    margin: 0;
    line-height: 1;
  }
  .product-title {
    position: absolute;
    top: 205px;
    left: 0;
    width: 500px;
    text-align: center;
    font-family: "Yellowtail", cursive;
    font-weight: 400;
    font-size: 84px;
    color: var(--indigo);
    margin: 0;
    line-height: 1;
  }
  .circle-copy {
    position: absolute;
    right: 42px;
    top: 425px;
    width: 290px;
    text-align: right;
    color: var(--white);
    font-family: "Bodoni Moda", "Times New Roman", serif;
  }
  .compat-headline {
    margin: 0;
    font-weight: 700;
    font-size: 25px;
    line-height: 36.5px;
  }
  .benefit {
    margin: 18px 0 0;
    font-weight: 400;
    font-size: 17.5px;
    line-height: 26px;
  }
  .ingredients {
    margin: 16px 0 0;
  }
  .ingredients-title {
    margin: 0;
    font-weight: 700;
    font-size: 14px;
    line-height: 20px;
  }
  .ingredients-list {
    margin: 2px 0 0;
    font-size: 12.5px;
    line-height: 17px;
  }
  .photo-placeholder {
    position: absolute;
    left: 62px;
    top: 640px;
    width: 240px;
    height: 455px;
    border-radius: 120px 120px 24px 24px;
    background: linear-gradient(160deg, var(--skin-light), var(--skin-mid));
  }
  .caution {
    position: absolute;
    left: 0;
    top: 1180px;
    width: 500px;
    text-align: center;
    color: var(--white);
    font-family: "Arimo", Arial, sans-serif;
    font-size: 14.5px;
    line-height: 18px;
    margin: 0;
  }
  .net-weight {
    position: absolute;
    left: 0;
    top: 1252px;
    width: 500px;
    text-align: center;
    color: var(--white);
    font-family: "Arimo", Arial, sans-serif;
    font-size: 17.5px;
    margin: 0;
  }
</style>
</head>
<body>
<div class="canvas">
  <div class="package">
    <svg class="package-shapes" viewBox="0 0 500 1295" aria-hidden="true">
      <defs>
        <linearGradient id="wave-fill" x1="0" y1="0" x2="1" y2="0">
          <stop offset="0" stop-color="var(--wave-start)"/>
          <stop offset="1" stop-color="var(--wave-end)"/>
        </linearGradient>
      </defs>
      <circle class="circle-outer" cx="357" cy="602" r="256" fill="var(--indigo)"/>
      <circle class="circle-inner" cx="382" cy="627" r="254" fill="var(--royal)"/>
      <path class="bottom-wave" d="M0 1085 C120 1060 230 1115 330 1108 C410 1102 460 1080 500 1070 L500 1295 L0 1295 Z" fill="url(#wave-fill)"/>
      <path class="wave-swoosh" d="M20 1102 C140 1090 250 1128 360 1120 C420 1116 460 1100 490 1088 C450 1112 400 1130 340 1134 C230 1140 130 1112 20 1102 Z" fill="var(--white)"/>
      <path class="wave-swoosh-thin" d="M40 1124 C150 1118 240 1146 350 1142 C300 1152 220 1150 40 1124 Z" fill="var(--white)"/>
    </svg>

    <h1 class="brand-name">By Selvane</h1>
    <h2 class="product-title">Paraffin Wax</h2>

    <div class="photo-placeholder" role="img" aria-label="Photograph of a bare foot held by two hands with red-painted nails"></div>

    <div class="circle-copy">
      <p class="compat-headline">Compatible for<br>use with most<br>wax paraffin heat<br>therapy units.</p>
      <p class="benefit">Deeply Moisturizes the<br>Skin Restoring a Healthier Look<br>and Feel to Skin.</p>
      <div class="ingredients">
        <p class="ingredients-title">Ingredients:</p>
        <p class="ingredients-list">Paraffin waxes and<br>Hydrocarbon waxes,<br>Petrolatum, Paraffin oils,<br>Apricot kernel oil,<br>Fragrance D &amp; C dyes.</p>
      </div>
    </div>

    <p class="caution">Caution:<br>Paraffin is flammable. Do not use near<br>open flame or an unprotected resistance heater.</p>
    <p class="net-weight">Net Wt. 1 lb. (450 g.)</p>
  </div>
</div>
</body>
</html>
```